Duct Manufacturing Company new to the industry needs business card and stationary design

we are sheet metal duct manufacturers looking for a business card design to fit my new business logo.
nothing to crazy that will date, but want it to stand out from the crowed.
I'm sure you guys will work it out.

Contact Information for Business Card

Glen Marsh
Director

Address
17 Dorwell St
Karrabee NSW 2791

0438 760 514

Sales@flowbend.com.au

Font styles to use
Other font styles liked:
• BankGothic md bt

Requirements
Nice to have
• Like the idea of corner rounded to match logo
• like to keep colours flowing
• font I like sharp square not rounded

```html
<!DOCTYPE html>
<html lang="en">
<head>
<meta charset="utf-8">
<title>Flowbend Industries – Business Card</title>
<link rel="stylesheet" href="https://fonts.googleapis.com/css2?family=Michroma&family=Questrial&display=swap">
<style>
  :root {
    --backdrop: #a3a2a2;
    --card: #fbfbfa;
    --brand-blue: #1a63b0;
    --deep-blue: #0f4f9c;
    --sky-blue: #1f8fd8;
    --leaf-green: #8cc63f;
    --forest-green: #1f9a45;
    --ink: #3d3d3d;
    --rule: #e2e2e2;
  }
  * { box-sizing: border-box; margin: 0; padding: 0; }
  html, body { width: 1200px; height: 1200px; overflow: hidden; }
  body {
    background: var(--backdrop);
    position: relative;
    font-family: "Questrial", sans-serif;
    color: var(--ink);
  }
  .card {
    position: absolute;
    width: 712px;
    height: 418px;
    background: var(--card);
    border-radius: 26px;
    overflow: hidden;
  }
  .card--front { left: 238px; top: 119px; }
  .card--back  { left: 230px; top: 644px; }

  .band { position: absolute; left: 0; bottom: 0; width: 712px; display: block; }

  /* front */
  .front-mark {
    position: absolute;
    left: 0; right: 0; top: 150px;
    display: flex; flex-direction: column; align-items: center; gap: 14px;
  }
  .front-mark__dot {
    width: 54px; height: 54px; border-radius: 50%;
    background: var(--brand-blue);
  }
  .front-mark__name {
    font-family: "Michroma", sans-serif;
    font-size: 30px;
    letter-spacing: 2px;
    color: var(--brand-blue);
    text-align: center;
    line-height: 1.35;
  }

  /* back */
  .back-mark {
    position: absolute;
    left: 40px; top: 160px; width: 300px;
    display: flex; align-items: center; gap: 14px;
  }
  .back-mark__dot {
    width: 40px; height: 40px; border-radius: 50%;
    background: var(--brand-blue); flex: none;
  }
  .back-mark__name {
    font-family: "Michroma", sans-serif;
    font-size: 22px;
    letter-spacing: 1px;
    color: var(--brand-blue);
    line-height: 1.3;
  }
  .divider {
    position: absolute;
    left: 369px; top: 42px; width: 1px; height: 278px;
    background: var(--rule);
  }
  .contact {
    position: absolute;
    left: 412px; top: 104px;
  }
  .contact__name {
    font-family: "Michroma", sans-serif;
    font-size: 21px;
    color: var(--brand-blue);
    letter-spacing: 1.5px;
    font-weight: 700;
  }
  .contact__role { font-size: 17px; margin-top: 6px; letter-spacing: 0.5px; }
  .contact__list { list-style: none; margin-top: 22px; font-size: 19px; letter-spacing: 0.6px; }
  .contact__list li { display: flex; align-items: center; gap: 14px; height: 27px; }
  .contact__list svg { width: 20px; height: 16px; flex: none; }
  .contact__address { font-size: 19px; letter-spacing: 0.6px; margin-top: 4px; line-height: 25px; }
  .web {
    position: absolute;
    right: 88px; bottom: 15px;
    color: #fff; font-size: 18px; letter-spacing: 0.6px;
  }
</style>
</head>
<body>

<section class="card card--front" aria-label="Card front">
  <div class="front-mark">
    <span class="front-mark__dot"></span>
    <p class="front-mark__name">FLOWBEND<br>INDUSTRIES</p>
  </div>
  <svg class="band" height="20" viewBox="0 0 712 20" aria-hidden="true">
    <defs>
      <linearGradient id="frontGreen" x1="0" x2="1">
        <stop offset="0" stop-color="#1f9a45"/>
        <stop offset="0.45" stop-color="#8cc63f"/>
        <stop offset="1" stop-color="#8cc63f"/>
      </linearGradient>
      <linearGradient id="frontBlue" x1="0" x2="1">
        <stop offset="0" stop-color="#1f8fd8"/>
        <stop offset="1" stop-color="#0f4f9c"/>
      </linearGradient>
    </defs>
    <polygon points="0,2 500,2 466,20 0,20" fill="url(#frontGreen)"/>
    <polygon points="504,2 712,2 712,20 470,20" fill="url(#frontBlue)"/>
  </svg>
</section>

<section class="card card--back" aria-label="Card back">
  <div class="back-mark">
    <span class="back-mark__dot"></span>
    <p class="back-mark__name">FLOWBEND<br>INDUSTRIES</p>
  </div>

  <div class="divider"></div>

  <div class="contact">
    <h1 class="contact__name">GLEN MARSH</h1>
    <p class="contact__role">Director</p>
    <ul class="contact__list">
      <li>
        <svg viewBox="0 0 20 16" aria-label="Phone"><path d="M2 6c0-3 16-3 16 0v2h-4V6H6v2H2z M5 9h10l2 6H3z" fill="#1a63b0"/></svg>
        0438 760 514
      </li>
      <li>
        <svg viewBox="0 0 20 16" aria-label="Email"><rect x="2" y="3" width="16" height="11" fill="#1a63b0"/><path d="M2 3l8 6 8-6" stroke="#fff" stroke-width="1.5" fill="none"/></svg>
        sales@flowbend.com.au
      </li>
    </ul>
    <p class="contact__address">17 Dorwell St<br>Karrabee NSW 2791</p>
  </div>

  <svg class="band" height="56" viewBox="0 0 712 56" aria-hidden="true">
    <defs>
      <linearGradient id="backBlue" x1="0" x2="1">
        <stop offset="0" stop-color="#0f4f9c"/>
        <stop offset="1" stop-color="#1a63b0"/>
      </linearGradient>
    </defs>
    <rect x="0" y="28" width="400" height="28" fill="#8cc63f"/>
    <polygon points="376,0 712,0 712,56 344,56" fill="url(#backBlue)"/>
  </svg>
  <p class="web">www.flowbend.com.au</p>
</section>

</body>
</html>
```